Staff Newsletter Template Image

We are looking for two .jpg images that we can put into a Word document and use for our staff newsletter. We will then add content using text boxes.
Attached is the current template which works for the columns and size that we need but we just want a fresh new design.
The Word document shows how we use it.
The name will stay the same - Brightwave Post but can be a different look to the current one.

Target Market(s)

Sales team

Colors

Designer to choose colors to be used in the design.

Requirements
Must have
• Colours will be green, grey and white, possibly cream if needed. All from the guidelines.
• I have attached our brand guidelines which shows design elements and fonts for our brand. Also attached is brand guidelines for one of our product lines as we would like to use the same green.
• It needs to be nice to look at and motivational for our team

```html
<!DOCTYPE html>
<html lang="en">
<head>
<meta charset="utf-8">
<title>Brightwave Post — Staff Newsletter</title>
<link rel="stylesheet" href="https://fonts.googleapis.com/css2?family=Cinzel:wght@500&display=swap">
<style>
  :root {
    --navy: #252b38;
    --green: #8dc63f;
    --green-deep: #5d8a3a;
    --paper-top: #ececed;
    --paper-bottom: #ffffff;
    --white: #ffffff;
  }
  html, body {
    margin: 0;
    padding: 0;
    overflow: hidden;
    background: var(--navy);
  }
  .newsletter {
    position: relative;
    width: 884px;
    height: 1200px;
    overflow: hidden;
    background: var(--navy);
  }
  .newsletter__page,
  .newsletter__band {
    position: absolute;
    inset: 0;
    width: 100%;
    height: 100%;
    display: block;
  }
  .newsletter__page {
    background: linear-gradient(180deg, var(--paper-top), var(--paper-bottom));
    clip-path: polygon(0 26.4%, 100% 15.9%, 100% 75.2%, 0 83.1%);
  }
  .newsletter__band--top {
    background: linear-gradient(90deg, var(--green) 0%, var(--green-deep) 55%, #34423a 100%);
    clip-path: polygon(0 19.1%, 100% 1.9%, 100% 15.9%, 0 26.4%);
  }
  .newsletter__band--bottom {
    background: linear-gradient(90deg, var(--green) 0%, var(--green-deep) 55%, #34423a 100%);
    clip-path: polygon(0 83.1%, 100% 75.2%, 100% 86.5%, 0 96.8%);
  }
  .masthead {
    position: absolute;
    left: 22px;
    top: 78px;
    margin: 0;
    font-family: "Cinzel", "Times New Roman", serif;
    font-weight: 500;
    font-size: 22px;
    letter-spacing: 0.5px;
    color: var(--white);
    white-space: nowrap;
  }
</style>
</head>
<body>
<main class="newsletter">
  <div class="newsletter__band newsletter__band--top" role="img" aria-label="Decorative green ribbon band across the header"></div>
  <div class="newsletter__page"></div>
  <div class="newsletter__band newsletter__band--bottom" role="img" aria-label="Decorative green ribbon band across the footer"></div>

  <h1 class="masthead">Brightwave Post</h1>
</main>
</body>
</html>
```